business card for a massage therapy practice named 'Cedar and Willow Massage Studio'

I really need a trendy, yet easy on the eyes business card to complement my logo. Ideally with some gold or rose gold foil work.

My uploaded file of the logo I have in horizontal but I have a vertical version as well. Another color that is used in the website is a blush pink here and there. I'd like to see some trendy tropical leaves in the design.

```html
<!DOCTYPE html>
<html lang="en">
<head>
<meta charset="utf-8">
<title>Cedar and Willow Massage Studio — Business Card</title>
<link href="https://fonts.googleapis.com/css2?family=Josefin+Sans:wght@300;400&display=swap" rel="stylesheet">
<style>
  :root {
    --bg: #efece7;
    --teal: #80c9b6;
    --teal-soft: #9bd6c6;
    --teal-line: #7cc6b3;
    --gold: #b39a63;
    --ink: #222222;
    --paper: #ffffff;
    --leaf-grey: #e6e4e1;
  }
  * { margin: 0; padding: 0; box-sizing: border-box; }
  html, body { width: 1200px; height: 795px; overflow: hidden; }
  body {
    background: var(--bg);
    font-family: "Josefin Sans", sans-serif;
    color: var(--ink);
    position: relative;
  }
  .card {
    position: absolute;
    top: 249px;
    width: 520px;
    height: 297px;
    overflow: hidden;
    box-shadow: 0 6px 18px rgba(0,0,0,0.12);
  }
  .card--front { left: 60px; background: var(--teal); }
  .card--back { left: 620px; background: var(--paper); }

  .leaf-art {
    position: absolute;
    border-radius: 46% 54% 40% 60%;
  }
  .card--front .leaf-art {
    left: 40px; top: 70px; width: 300px; height: 200px;
    background: radial-gradient(ellipse at center, var(--teal-soft) 0%, rgba(155,214,198,0) 70%);
  }
  .card--back .leaf-art {
    left: 20px; top: -10px; width: 260px; height: 160px;
    background: radial-gradient(ellipse at center, var(--leaf-grey) 0%, rgba(230,228,225,0) 70%);
  }

  .brand {
    position: absolute;
    display: flex;
    align-items: center;
    gap: 12px;
  }
  .brand__dot {
    width: 26px; height: 26px; border-radius: 50%;
    background: var(--gold);
    flex: none;
  }
  .brand__name {
    font-weight: 400;
    color: var(--ink);
    line-height: 1.15;
  }
  .brand__name span { display: block; }
  .card--front .brand { left: 165px; top: 118px; }
  .card--front .brand__name { font-size: 24px; }
  .card--front .brand__name .brand__sub { font-size: 12px; letter-spacing: 3px; }
  .card--back .brand { right: 26px; top: 30px; }
  .card--back .brand__dot { width: 20px; height: 20px; }
  .card--back .brand__name { font-size: 17px; }
  .card--back .brand__name .brand__sub { font-size: 9px; letter-spacing: 2.5px; }

  .rule {
    position: absolute;
    left: 28px; right: 120px; top: 150px;
    height: 1.5px; background: var(--teal-line);
  }
  .holder {
    position: absolute; right: 26px; top: 164px;
    font-size: 17px; font-weight: 300; letter-spacing: 0.5px;
    color: var(--teal-line); text-transform: uppercase;
  }
  .contact {
    position: absolute; right: 26px; top: 194px;
    list-style: none; text-align: right;
    font-size: 14px; font-weight: 300; line-height: 22px;
  }
  .contact li { display: flex; align-items: center; justify-content: flex-end; gap: 7px; }
  .contact .phone { font-size: 17px; font-weight: 400; }
  .icon { width: 14px; height: 14px; flex: none; }

  .social {
    position: absolute; left: 28px; top: 172px;
    list-style: none; font-size: 14px; font-weight: 300; line-height: 24px;
  }
  .social li { display: flex; align-items: center; gap: 8px; }
  .social__mark { width: 14px; height: 14px; border-radius: 50%; background: var(--teal-line); }
</style>
</head>
<body>
  <section class="card card--front" aria-label="Card front">
    <div class="leaf-art" role="img" aria-label="Faint tropical pineapple and leaf illustration"></div>
    <div class="brand">
      <span class="brand__dot"></span>
      <p class="brand__name"><span>Cedar &amp; Willow</span><span class="brand__sub">MASSAGE STUDIO</span></p>
    </div>
  </section>

  <section class="card card--back" aria-label="Card back">
    <div class="leaf-art" role="img" aria-label="Faint grey tropical pineapple and leaf illustration"></div>
    <div class="brand">
      <span class="brand__dot"></span>
      <p class="brand__name"><span>Cedar &amp; Willow</span><span class="brand__sub">MASSAGE STUDIO</span></p>
    </div>
    <div class="rule"></div>
    <p class="holder">Marisol Bennett LMT</p>
    <ul class="contact">
      <li class="phone">
        <svg class="icon" viewBox="0 0 16 16"><path fill="#7cc6b3" d="M3.5 1.5l2.5 0 1 3.5-1.6 1.2a9 9 0 0 0 4.4 4.4L11 9l3.5 1v2.5c0 1-1 2-2 2A11 11 0 0 1 1.5 3.5c0-1 1-2 2-2z"/></svg>
        916.555.0142
      </li>
      <li>www.cedarandwillow.com
        <svg class="icon" viewBox="0 0 16 16"><circle cx="8" cy="8" r="8" fill="#7cc6b3"/><g fill="none" stroke="#fff" stroke-width="1"><circle cx="8" cy="8" r="4.5"/><ellipse cx="8" cy="8" rx="2" ry="4.5"/><line x1="3.5" y1="8" x2="12.5" y2="8"/></g></svg>
      </li>
      <li>cedarandwillow@mail.com
        <svg class="icon" viewBox="0 0 16 16"><circle cx="8" cy="8" r="8" fill="#7cc6b3"/><g fill="none" stroke="#fff" stroke-width="1"><rect x="4" y="5" width="8" height="6"/><polyline points="4,5 8,8.5 12,5"/></g></svg>
      </li>
    </ul>
    <ul class="social">
      <li><span class="social__mark"></span>@cedarandwillow</li>
      <li><span class="social__mark"></span>@cedarandwillow</li>
    </ul>
  </section>
</body>
</html>
```